Merrisol. Sunless Tanning Mousse Label

I'm looking for a label creation for a new brand of sunless tanning solutions. They are in 6.7oz bottles (template attached).

For the front of the bottle (see template) I would like an abstract multi coloured design taking up just over half the top of the bottle (approx 60%) and going around the design (this is similar to the design inspiration attached). I would this design to use the attached colour palette of pinks. It can be swirls, drips, squares, lines, whatever you think will look good.

The logo will then be over top of that abstract design in the upper 1/3, in the colour #3fe0d0

Under the abstract design the following text:

Amber Hush (Larger text)
Violet Base (2nd heading)
1 Hour Sunless Mousse (Sub text)
The No Orange Guarantee! (Sub text)
Vegan Formula (sub text)

The sub texts for above can be fun, have coloured background, different fonts, whatever looks good and is sill fun.

Towards the bottom of the front of bottle we require the sizing information:

200ml 6.7 Fl Oz

On the left side of the front (so in the template the middle smaller section) I would like the phrase "You ain't gotta get ready if you stay ready" Could you please make this as a separate little quote, with a fun design to it. It's like a little hidden gem on the side of the bottle.

On the back of the bottle for now can you please start towards the top with:

Amber Hush Mousse (larger)
Violet base (second heading)
Deep Mediterranean Inspired Tan (second heading)
Easy to Apply & Streak Free
Vegan friendly & 100% natural DHA tan actives

Under this I require approx 1.5" of Lorem Ipsum for now which will take the place of directions for using the product.

Under that in small writing can we include "Warning: This product does not contain a sunscreen and will not protect against sunburn. For external use only. If skin irritation occurs, discontinue use. Carry out a patch test 24 hours prior to full body use. Store below 25(degrees sign)C."

At the bottom is the smallest yet still legible writing, can we include the ingredients that are listed below.

Target Market(s)

Females 24-35 who take care of themselves and always want to look good. It's a youthful fun product.

Requirements
Must have
• Bright colours, and just screams FUN and youthful.

Ingredients must be listed on the back. They dont' need to take up more than an inch in height, less if possible.
*******************************************

INGREDIENTS: Water (Aqua), Propylene Glycol, Dihydroxyacetone, Peg-6 Caprylic/Capric Glycerides, Dihydroxypropyl Peg-5 Linoleammonium Chloride, Peg-7 Glyceryl Cocoate, Caramel,
Phenoxyethanol, Caprylyl Glycol, Potassium Sorbate, Hexylene Glycol, Glycerin, Helianthus Annuus (Sunflower) Seed Oil, Beta Vulgaris (Beet) Root Extract, Panthenol, Solanum Lycopersicum
(Tomato) Fruit Extract, Vaccinium Macrocarpon (Cranberry) Fruit Extract, L-ascorbic Acid (Vitamin C), Tocopheryl Acetate (Vitamin E), Theobroma Cacao (Cocoa) Seed Butter, Rosa Canina (Rose Hip)
Fruit Oil, Glycine Soja (Soybean) Oil, Cucumis Sativus (Cucumber) Fruit Extract, Blue 1 (CI 42090), Red 40 (CI 16035), Yellow 6 (CI 15985), Green 5 (CI 61570), Yellow 5 (CI 19140), Red 33 (CI 17200)

*****************************
Nice to have
• Several options to choose from, some can include a gradient into geometric shapes, rather than solid colour. Experiment
Should not have
• Do not want it to look medical.
Want colours to stay in the same pink family for the abstract design - can use white also.

```html
<!DOCTYPE html>
<html lang="en">
<head>
<meta charset="utf-8">
<title>Merrisol Sunless Tanning Mousse Labels</title>
<link href="https://fonts.googleapis.com/css2?family=Josefin+Sans:wght@300;400;600&family=Montserrat:wght@800&family=Oswald:wght@300&family=Pacifico&display=swap" rel="stylesheet">
<style>
  :root {
    --page: #ececec;
    --pink: #ec5f98;
    --pink-deep: #d43f7f;
    --pink-light: #f79cc0;
    --blush: #fbc3d8;
    --berry: #b02a66;
    --white: #ffffff;
    --logo: #3fe0d0;
    --tag-text: #e0508c;
  }
  * { margin: 0; padding: 0; box-sizing: border-box; }
  html, body { width: 1200px; height: 810px; overflow: hidden; }
  body {
    background: var(--page);
    font-family: "Josefin Sans", sans-serif;
    color: var(--white);
    position: relative;
  }
  .label-row {
    position: absolute;
    top: 144px;
    left: 15px;
    display: flex;
    gap: 30px;
  }
  .label {
    position: relative;
    width: 210px;
    height: 522px;
    overflow: hidden;
    background: var(--pink);
  }
  .pattern { position: absolute; inset: 0; }
  .pattern--swirls {
    background: radial-gradient(circle at 40% 40%, var(--pink-light), var(--pink) 70%);
  }
  .pattern--streaks {
    background: linear-gradient(135deg, var(--pink-light) 0%, var(--pink-deep) 35%, var(--pink-light) 60%, var(--pink) 100%);
  }
  .pattern--waves {
    background: linear-gradient(160deg, var(--pink) 0%, var(--blush) 30%, var(--pink-deep) 55%, var(--blush) 80%, var(--pink) 100%);
  }
  .pattern--stripes {
    background: linear-gradient(90deg, var(--pink) 0%, var(--berry) 25%, var(--pink-deep) 50%, var(--berry) 75%, var(--pink) 100%);
  }
  .pattern--plain {
    background: linear-gradient(180deg, var(--pink-light) 0%, var(--pink) 40%, var(--pink-deep) 100%);
  }
  .brand {
    position: absolute;
    left: 0; right: 0;
    text-align: center;
    font-family: "Josefin Sans", sans-serif;
    font-weight: 600;
    font-size: 27px;
    letter-spacing: 0.5px;
    color: var(--logo);
  }
  .front .brand { top: 48px; }
  .back .brand { top: 36px; }
  .product-name {
    position: absolute;
    left: 0; right: 0;
    text-align: center;
    font-family: "Montserrat", sans-serif;
    font-weight: 800;
    font-size: 56px;
    line-height: 1;
    color: var(--white);
  }
  .front .product-name { top: 334px; }
  .back .product-name { top: 96px; }
  .variant-tag {
    position: absolute;
    left: 30px;
    width: 148px;
    height: 20px;
    background: var(--white);
    color: var(--tag-text);
    font-size: 10px;
    letter-spacing: 4.5px;
    text-align: center;
    line-height: 22px;
    padding-left: 4px;
  }
  .front .variant-tag { top: 396px; }
  .back .variant-tag { top: 152px; }
  .claims {
    position: absolute;
    left: 0; right: 0;
    top: 430px;
    text-align: center;
    font-weight: 300;
    font-size: 10.5px;
    line-height: 13px;
  }
  .size {
    position: absolute;
    left: 0; right: 0;
    top: 494px;
    text-align: center;
    font-family: "Oswald", sans-serif;
    font-weight: 300;
    font-size: 14px;
  }
  .benefits {
    position: absolute;
    left: 4px; right: 4px;
    top: 182px;
    text-align: center;
    font-weight: 400;
    font-size: 9px;
    line-height: 14px;
  }
  .directions {
    position: absolute;
    left: 10px; right: 10px;
    top: 230px;
    text-align: justify;
    font-weight: 300;
    font-size: 5.6px;
    line-height: 9px;
  }
  .warning {
    position: absolute;
    left: 8px; right: 8px;
    top: 276px;
    height: 64px;
    border: 0.6px solid rgba(255,255,255,0.8);
    border-radius: 2px;
    padding: 4px 4px;
    text-align: center;
    font-weight: 300;
    font-size: 5.4px;
    line-height: 8.5px;
  }
  .warning-title { font-weight: 600; font-size: 7.5px; line-height: 10px; }
  .ingredients {
    position: absolute;
    left: 8px; right: 8px;
    top: 348px;
    text-align: justify;
    font-weight: 300;
    font-size: 5.2px;
    line-height: 8px;
  }
  .ingredients-title {
    display: block;
    text-align: center;
    font-weight: 600;
    font-size: 6.5px;
  }
  .side-quote {
    position: absolute;
    left: 22px; right: 22px;
    top: 456px;
    padding: 3px 6px;
    border-radius: 10px;
    background: var(--white);
    color: var(--pink-deep);
    font-family: "Pacifico", cursive;
    font-size: 8px;
    line-height: 12px;
    text-align: center;
  }
</style>
</head>
<body>
<div class="label-row">

  <section class="label front">
    <div class="pattern pattern--swirls" role="img" aria-label="Repeating swirl pattern in pink tones"></div>
    <div class="brand">Merrisol</div>
    <div class="product-name">HUSH</div>
    <div class="variant-tag">VIOLET BASE</div>
    <div class="claims">1 Hour Sunless Mousse<br>The No Orange Guarantee!<br>Vegan Formula</div>
    <div class="size">200ml ℮ 6.7 Fl Oz</div>
  </section>

  <section class="label front">
    <div class="pattern pattern--streaks" role="img" aria-label="Diagonal brushed streak pattern in pink tones"></div>
    <div class="brand">Merrisol</div>
    <div class="product-name">HUSH</div>
    <div class="variant-tag">VIOLET BASE</div>
    <div class="claims">1 Hour Sunless Mousse<br>The No Orange Guarantee!<br>Vegan Formula</div>
    <div class="size">200ml ℮ 6.7 Fl Oz</div>
  </section>

  <section class="label front">
    <div class="pattern pattern--waves" role="img" aria-label="Flowing wave pattern in pink and blush tones"></div>
    <div class="brand">Merrisol</div>
    <div class="product-name">HUSH</div>
    <div class="variant-tag">VIOLET BASE</div>
    <div class="claims">1 Hour Sunless Mousse<br>The No Orange Guarantee!<br>Vegan Formula</div>
    <div class="size">200ml ℮ 6.7 Fl Oz</div>
  </section>

  <section class="label front">
    <div class="pattern pattern--stripes" role="img" aria-label="Vertical stripe pattern in pink and berry tones"></div>
    <div class="brand">Merrisol</div>
    <div class="product-name">HUSH</div>
    <div class="variant-tag">VIOLET BASE</div>
    <div class="claims">1 Hour Sunless Mousse<br>The No Orange Guarantee!<br>Vegan Formula</div>
    <div class="size">200ml ℮ 6.7 Fl Oz</div>
  </section>

  <section class="label back">
    <div class="pattern pattern--plain"></div>
    <div class="brand">Merrisol</div>
    <div class="product-name">HUSH</div>
    <div class="variant-tag">VIOLET BASE</div>
    <div class="benefits">Deep Mediterranean Inspired Tan<br>Easy to Apply &amp; Streak Free<br>Vegan friendly &amp; 100% natural DHA tan actives</div>
    <p class="directions">Lorem Ipsum is simply dummy text of the printing and typesetting industry. Lorem Ipsum has been the industry's standard dummy text ever since the 1500s, when an unknown printer took a galley of type and scrambled it to make a type specimen book.</p>
    <div class="warning">
      <div class="warning-title">WARNING:</div>
      This product does not contain a sunscreen and will not protect against sunburn. For external use only. If skin irritation occurs, discontinue use. Carry out a patch test 24 hours prior to full body use. Store below 25°C.
    </div>
    <p class="ingredients"><span class="ingredients-title">INGREDIENTS:</span>Water (Aqua), Propylene Glycol, Dihydroxyacetone, Peg-6 Caprylic/Capric Glycerides, Dihydroxypropyl Peg-5 Linoleammonium Chloride, Peg-7 Glyceryl Cocoate, Caramel, Phenoxyethanol, Caprylyl Glycol, Potassium Sorbate, Hexylene Glycol, Glycerin, Helianthus Annuus (Sunflower) Seed Oil, Beta Vulgaris (Beet) Root Extract, Panthenol, Solanum Lycopersicum (Tomato) Fruit Extract, Vaccinium Macrocarpon (Cranberry) Fruit Extract, L-ascorbic Acid (Vitamin C), Tocopheryl Acetate (Vitamin E), Theobroma Cacao (Cocoa) Seed Butter, Rosa Canina (Rose Hip) Fruit Oil, Glycine Soja (Soybean) Oil, Cucumis Sativus (Cucumber) Fruit Extract, Blue 1 (CI 42090), Red 40 (CI 16035), Yellow 6 (CI 15985), Green 5 (CI 61570), Yellow 5 (CI 19140), Red 33 (CI 17200)</p>
    <div class="side-quote">“You ain't gotta get ready<br>if you stay ready”</div>
    <div class="size">200ml ℮ 6.7 Fl Oz</div>
  </section>

</div>
</body>
</html>
```